Modern Business Card for Larkwell 2018

Our company assumes the best about people. We are creating an online community of entrepreneurs and business leaders who struggle with marketing their business online.

This business card should POP! We recently got a new logo and are launching a new website next month, so our business cards should make a statement that feels:
-Fresh
-Smart
-Trustworthy
-Fun

Target Market(s)

small business owners, entrepreneurs

Industry/Entity Type

Digital Marketing

Contact Information for Business Card

Dimensions: 3.5" x 2"

Font styles to use
Sans Serif

Colors
f37122
ffffff

Requirements
Must have
• We need a business card with a modern, bold design. We will use one side of the card as a lead-generation offer, so text on one side will need to fit up to 140 characters. The business card should stick to our core colors (orange, black, and white).
Nice to have
• We think a vertical "portrait" design could be interesting.
Should not have
• Should not look like a traditional business card. The round icon should stand out from a distance.

```html
<!DOCTYPE html>
<html lang="en">
<head>
<meta charset="utf-8">
<title>Larkwell Business Card</title>
<link href="https://fonts.googleapis.com/css2?family=PT+Sans:wght@400;700&display=swap" rel="stylesheet">
<style>
  :root {
    --orange: #e86424;
    --white: #f4f4f4;
    --paper: #ffffff;
    --backdrop: #2e2e2e;
    --rule: #2a2a2a;
  }
  * { box-sizing: border-box; }
  html, body {
    margin: 0;
    width: 1200px;
    height: 960px;
    overflow: hidden;
    background: var(--backdrop);
    font-family: "PT Sans", Arial, sans-serif;
  }
  .card {
    position: absolute;
    width: 598px;
    height: 342px;
    overflow: hidden;
  }
  .card-front { left: 322px; top: 108px; background: var(--white); }
  .card-back { left: 320px; top: 493px; background: var(--orange); color: var(--paper); }
  .front-swoosh { position: absolute; inset: 0; }

  .brand { position: absolute; display: flex; align-items: center; }
  .brand-dot { border-radius: 50%; flex: none; }
  .brand-name { font-weight: 700; line-height: 1; }

  .card-front .brand { left: 46px; top: 85px; gap: 16px; }
  .card-front .brand-dot { width: 84px; height: 84px; background: var(--orange); }
  .card-front .brand-name { color: var(--orange); font-size: 44px; }

  .contact {
    position: absolute;
    right: 25px;
    top: 254px;
    text-align: right;
    color: var(--paper);
  }
  .contact-name { font-size: 22px; font-weight: 700; margin: 0; line-height: 1.1; text-transform: uppercase; }
  .contact-role { font-size: 15px; font-weight: 700; margin: 6px 0 0; text-transform: uppercase; }
  .contact-email { font-size: 15px; margin: 2px 0 0; }

  .card-back .brand { left: 26px; top: 80px; gap: 12px; }
  .card-back .brand-dot { width: 68px; height: 68px; background: var(--paper); }
  .card-back .brand-name { color: var(--paper); font-size: 32px; }

  .back-divider {
    position: absolute;
    left: 263px; top: 30px;
    width: 1px; height: 167px;
    background: rgba(255,255,255,0.55);
  }
  .offer { position: absolute; left: 297px; top: 30px; width: 290px; }
  .offer-headline {
    margin: 0;
    font-size: 20px;
    font-weight: 700;
    line-height: 21px;
    text-transform: uppercase;
  }
  .offer-body { margin: 6px 0 0; font-size: 15px; line-height: 20px; }
  .offer-url { margin: 10px 0 0; font-size: 19px; font-weight: 700; }

  .notes {
    position: absolute;
    left: 20px; top: 217px;
    width: 557px; height: 102px;
    border-radius: 14px;
    background: var(--white);
  }
  .notes-line {
    position: absolute;
    left: 24px; right: 27px;
    height: 1px;
    background: var(--rule);
  }
  .notes-line.first { top: 31px; }
  .notes-line.second { top: 71px; }
</style>
</head>
<body>
  <section class="card card-front">
    <svg class="front-swoosh" width="598" height="342" viewBox="0 0 598 342" aria-hidden="true">
      <path d="M128,342 C330,290 480,180 518,0 L598,0 L598,342 Z" fill="var(--orange)"/>
      <path d="M150,342 C345,282 462,172 476,0 L484,0 C472,178 360,292 188,342 Z" fill="var(--orange)"/>
    </svg>
    <div class="brand">
      <span class="brand-dot"></span>
      <span class="brand-name">Larkwell</span>
    </div>
    <div class="contact">
      <p class="contact-name">Dana Whitfield</p>
      <p class="contact-role">Story Marketing Coach</p>
      <p class="contact-email">dana@larkwellnow.com</p>
    </div>
  </section>

  <section class="card card-back">
    <div class="brand">
      <span class="brand-dot"></span>
      <span class="brand-name">Larkwell</span>
    </div>
    <div class="back-divider"></div>
    <div class="offer">
      <h2 class="offer-headline">Reach more people.<br>Make more money.<br>Create more impact.</h2>
      <p class="offer-body">Get your free Larkwell<br>Starter Package and our<br>marketing guide today at</p>
      <p class="offer-url">Larkwellnow.com/start</p>
    </div>
    <div class="notes">
      <div class="notes-line first"></div>
      <div class="notes-line second"></div>
    </div>
  </section>
</body>
</html>
```